Alaska Law Firm Needs a Sticker Design

We need a design for stickers to put on already-printed brochures. We mail the brochures to potential clients so they can learn more about accident-induced injuries, insurance claims, legal representation, and our own law firm.

One of our lawyers wrote a book that provides a helpful overview of personal injury claims. We are offering this book for free to anyone who calls and requests it. Therefore, the sticker design should include one of the following phrases, or something very similar:
a) "Still have questions? Call and request our book-- for free!"
b) "Still have questions about auto accident claims? Call and request our book today."
c) "Still have questions about filing a claim? Call and request a free copy of our book."
d) "Still have questions? Call us today to request a free copy of our book, Clear Lanes Ahead."
e) "To learn more about automobile accidents and insurance, call today and request a free copy of our book."

The sticker should be approximately 3"x3" and may be a circle, square, rectangle, or ellipsis. The sticker will be placed on the back of the folder, which is light blue. We would like the sticker to match the color scheme of our website and the folder.

I will upload an image of the book cover as soon as I obtain it.

Law Firm

Font styles to use
Serif
Sans Serif

Requirements
Should not have
• Bright colors that aren't already used in the folder design. e.g. no bright orange, pink, chartreuse, turquoise, yellow, red.

```html
<!DOCTYPE html>
<html lang="en">
<head>
<meta charset="utf-8">
<title>Free Book Sticker</title>
<link rel="stylesheet" href="https://fonts.googleapis.com/css2?family=Open+Sans:ital,wght@0,400;0,800;1,400;1,700&display=swap">
<style>
  :root {
    --navy: #0f3d6b;
    --book-blue: #0a58a0;
    --spine-blue: #0b467f;
    --white: #ffffff;
    --page-white: #f4f6f9;
  }
  html, body {
    margin: 0;
    padding: 0;
    width: 1200px;
    height: 1200px;
    overflow: hidden;
    background: var(--white);
  }
  .sticker {
    display: block;
    width: 1200px;
    height: 1200px;
    font-family: "Open Sans", Arial, sans-serif;
  }
  .sticker-base { fill: var(--navy); }
  .sticker-ring { fill: none; stroke: var(--white); stroke-width: 10; }
  .book-cover { fill: var(--book-blue); }
  .book-spine { fill: var(--spine-blue); }
  .book-title-bar { fill: var(--white); }
  .book-pages { fill: var(--page-white); }
  .text { fill: var(--white); text-anchor: middle; }
  .lead { font-style: italic; font-weight: 400; font-size: 45px; }
  .prompt { font-weight: 400; font-size: 47px; }
  .free { font-weight: 800; font-size: 172px; letter-spacing: -2px; }
  .book-name { font-style: italic; font-weight: 700; font-size: 64px; }
  .divider { fill: var(--white); }
</style>
</head>
<body>
<svg class="sticker" viewBox="0 0 1200 1200" xmlns="http://www.w3.org/2000/svg" role="img" aria-label="Still have questions? Call and request a free copy of our book, Clear Lanes Ahead">
  <defs>
    <clipPath id="sticker-inner">
      <circle cx="600" cy="600" r="573"/>
    </clipPath>
    <filter id="book-shadow" x="-10%" y="-10%" width="130%" height="130%">
      <feDropShadow dx="-6" dy="6" stdDeviation="8" flood-color="#000" flood-opacity="0.45"/>
    </filter>
    <radialGradient id="emblem-fill" cx="50%" cy="45%" r="60%">
      <stop offset="0%" stop-color="#ffffff"/>
      <stop offset="100%" stop-color="#e6edf5"/>
    </radialGradient>
  </defs>

  <circle class="sticker-base" cx="600" cy="600" r="597"/>
  <circle class="sticker-ring" cx="600" cy="600" r="582"/>

  <g class="book" clip-path="url(#sticker-inner)">
    <rect class="book-cover" x="516" y="91" width="760" height="1018" rx="16" filter="url(#book-shadow)"/>
    <rect class="book-spine" x="575" y="151" width="12" height="793" rx="3"/>
    <rect class="book-title-bar" x="683" y="260" width="520" height="49"/>
    <rect class="book-title-bar" x="732" y="331" width="392" height="49"/>
    <circle cx="920" cy="620" r="151" fill="url(#emblem-fill)" role="img" aria-label="Car emblem on the book cover"/>
    <rect class="book-pages" x="544" y="984" width="700" height="89" rx="44"/>
  </g>

  <g class="message">
    <text class="text lead" x="291" y="274">Still have</text>
    <text class="text lead" x="291" y="334">questions?</text>
    <text class="text prompt" x="291" y="448">Call and request a</text>
    <text class="text free" x="291" y="613">FREE</text>
    <text class="text prompt" x="291" y="676">copy of our book!</text>
    <rect class="divider" x="93" y="721" width="422" height="6"/>
    <text class="text book-name" x="299" y="834">Clear Lanes</text>
    <text class="text book-name" x="299" y="918">Ahead</text>
  </g>
</svg>
</body>
</html>
```